Membership Based Medical Practice Website

We need a functioning website for a new Membership based medical practice. There will be an enrollment fee and a monthly fee. We would like to see designs that are modern, simple. Should use neutral light colors. Examples of sites we like are www.kellanmoorclinic.com and https://fernholtcare.com/ We also have a link that when "Join Now" is clicked it will go to the signup website.

Target Market(s)

Gay Men, local population, Age group 20 to 60's.

Industry/Entity Type

Medical

Coding

Coded - Design and coding required

Number of Pages Required

5+ page

Font styles to use
Sans Serif

Colors
ffffff
cee9f5
ecf7fb
cfeae6
edf8f6
aaaaaa
e9e9e9
dbdbdb
fff3d1

Requirements
Must have
• Logo and header on every page. Clean, simple design, clear content, mobile compatible.
• Must use Wordpress
Nice to have
• Ideas should come from kellanmoorclinic.com
• Easy to read
Should not have
• Generic patient pictures, bold colors.
• Should not copy from above websites.

```html
<!DOCTYPE html>
<html lang="en">
<head>
<meta charset="utf-8">
<title>Larkfield Infectious Disease Specialists</title>
<link href="https://fonts.googleapis.com/css2?family=Lato:wght@300;400;700&display=swap" rel="stylesheet">
<style>
:root{
  --white:#ffffff;
  --ink:#1c1c1c;
  --body:#3a3a3a;
  --grey:#aaaaaa;
  --line:#dbdbdb;
  --sky:#cee9f5;
  --sky-soft:#ecf7fb;
  --mint:#cfeae6;
  --mint-soft:#edf8f6;
  --cream:#fff3d1;
  --gold:#e8cf78;
  --footer:#e6f3f9;
  --icon:#6f6f6f;
}
*{margin:0;padding:0;box-sizing:border-box}
html,body{width:1200px;height:2731px;overflow:hidden;background:var(--white)}
body{font-family:'Lato',sans-serif;color:var(--ink);position:relative}
.abs{position:absolute}

/* header + hero */
.hero{left:0;top:0;width:1200px;height:694px;
  background:linear-gradient(180deg,#d9dcdf 0%,#c9cdd0 30%,#9ea59a 48%,#6e7a5e 58%,#3a3d3c 72%,#2a2b2c 100%)}
.brand{left:104px;top:46px;display:flex;align-items:center;gap:16px}
.brand-mark{width:70px;height:70px;border:2px solid #c9a94c;border-radius:50%}
.brand-name{font-weight:300;color:var(--ink);line-height:1.2}
.brand-name .top{display:block;font-size:24px;letter-spacing:12px}
.brand-name .bottom{display:block;font-size:17px;letter-spacing:.5px}
.main-nav{left:508px;top:55px;width:437px;display:flex;align-items:center;justify-content:space-between}
.main-nav a{font-size:15px;color:var(--ink);text-decoration:none;white-space:nowrap}
.join{left:954px;top:44px;width:100px;height:43px;border-radius:22px;background:var(--sky);
  font-size:15px;display:flex;align-items:center;justify-content:center;color:var(--ink);text-decoration:none}
.hero-title{left:0;top:282px;width:1200px;text-align:center;font-size:36px;font-weight:400;line-height:1.2;color:var(--ink)}
.slide-arrow{top:304px;width:54px;height:54px;border-radius:50%;background:rgba(90,90,90,.55)}
.slide-arrow svg{display:block}

/* expertise */
.section-title{left:0;width:1200px;text-align:center;font-weight:400;font-size:27px;line-height:1.4;color:var(--ink)}
.gold-rule{left:570px;top:846px;width:60px;height:3px;background:var(--gold)}
.lead{left:0;top:877px;width:1200px;text-align:center;font-size:21px;font-weight:300;color:var(--grey)}
.areas{top:964px;text-align:center;font-size:17px;line-height:36.5px;color:var(--ink)}

/* benefits band */
.band{left:0;top:1160px;width:1200px;height:783px}
.band-title{left:0;top:1230px;width:1200px;text-align:center;font-size:31px;font-weight:400;color:var(--ink)}
.band-sub{left:0;top:1278px;width:1200px;text-align:center;font-size:21px;font-weight:400;color:var(--ink)}
.band-rule{left:554px;top:1318px;width:92px;height:2px;background:#5a5a5a}
.feature{width:160px}
.feature svg{display:block;height:50px}
.feature h3{font-size:18px;font-weight:700;color:#333;line-height:1.3;margin-top:16px}
.feature p{font-size:14.5px;color:#444;line-height:1.35;margin-top:12px}

/* pricing */
.photo-ring{left:118px;top:2036px;width:394px;height:394px;border-radius:50%;border:2px solid var(--mint)}
.photo{left:133px;top:2051px;width:364px;height:364px;border-radius:50%;
  background:radial-gradient(circle at 50% 85%,#fbe3a6 0%,#f2b063 25%,#c98a5a 45%,#a6899a 70%,#d6cde0 100%)}
.price-title{left:552px;top:2044px;font-size:28px;font-weight:400;line-height:1.3;color:var(--ink)}
.price-sub{left:552px;top:2125px;font-size:21px;font-weight:300;color:var(--grey)}
.perks{left:552px;top:2170px;list-style:none;font-size:17px;color:#333;width:420px}
.perks li{position:relative;padding-left:20px;line-height:22px;margin-bottom:9px}
.perks li svg{position:absolute;left:0;top:5px}
.learn{left:543px;top:2387px;width:175px;height:50px;border-radius:25px;background:var(--cream);
  font-size:16px;font-weight:700;color:#333;display:flex;align-items:center;justify-content:center;text-decoration:none}

/* footer */
.footer{left:0;top:2510px;width:1200px;height:221px}
.foot-nav{left:0;top:2586px;width:1200px;text-align:center;font-size:20px}
.foot-nav a{color:var(--ink);text-decoration:none;margin:0 10px}
.copy{left:0;top:2621px;width:1200px;text-align:center;font-size:13px;color:#333}
.social{left:513px;top:2656px;display:flex;gap:6px}
.social span{width:38px;height:38px;border-radius:50%;border:1.5px solid #555;display:block}
</style>
</head>
<body>

<header>
  <div class="abs hero" role="img" aria-label="Photograph of an open road through green misty hills with grazing sheep"></div>
  <div class="abs brand">
    <span class="brand-mark"></span>
    <span class="brand-name"><span class="top">LARKFIELD</span><span class="bottom">INFECTIOUS DISEASE SPECIALISTS</span></span>
  </div>
  <nav class="abs main-nav">
    <a href="#">HOME</a><a href="#">SPECIALTIES</a><a href="#">PRICING</a><a href="#">ABOUT US</a><a href="#">FAQ</a><a href="#">BLOG</a>
  </nav>
  <a class="abs join" href="#">JOIN US</a>
  <h1 class="abs hero-title">SPECIALTY MEDICINE WITH COMMITMENT,<br>COMPASSION AND CARE</h1>
  <a class="abs slide-arrow" style="left:115px" href="#" aria-label="Previous slide"><svg width="54" height="54" viewBox="0 0 54 54"><path d="M31 18 L22 27 L31 36" fill="none" stroke="#fff" stroke-width="2.5"/></svg></a>
  <a class="abs slide-arrow" style="left:1014px" href="#" aria-label="Next slide"><svg width="54" height="54" viewBox="0 0 54 54"><path d="M23 18 L32 27 L23 36" fill="none" stroke="#fff" stroke-width="2.5"/></svg></a>
</header>

<section class="expertise">
  <h2 class="abs section-title" style="top:757px">WE OFFER COMPREHENSIVE TREATMENT OF A WIDE<br>VARIETY OF INFECTIOUS DISEASES.</h2>
  <div class="abs gold-rule"></div>
  <p class="abs lead">Out expertise is in the following area.</p>
  <div class="abs areas" style="left:120px;width:280px">HIV/PrEP<br>Chronic Hepatitis<br>Sexually transmitted infections</div>
  <div class="abs areas" style="left:406px;width:360px">Pre-travel vaccinations and counselling<br>Infections associated with medical devices<br>Bone and Joint infections</div>
  <div class="abs areas" style="left:783px;width:280px">Postsurgical infections<br>Diabetes related infections<br>Tuberculosis</div>
</section>

<section class="benefits">
  <svg class="abs band" width="1200" height="783" viewBox="0 0 1200 783" aria-hidden="true">
    <defs><linearGradient id="bandFill" x1="0" y1="0" x2="1" y2="1">
      <stop offset="0" stop-color="#c2e2f2"/><stop offset="1" stop-color="#c7e9e2"/></linearGradient></defs>
    <path d="M0 22 H520 C555 22 560 0 600 0 C640 0 645 22 680 22 H1200 V783 H0 Z" fill="url(#bandFill)"/>
  </svg>
  <h2 class="abs band-title">LESS WAIT, MORE PERSONAL.</h2>
  <p class="abs band-sub">WE ARE NOT YOUR TRADITIONAL DOCTOR’S OFFICE.</p>
  <div class="abs band-rule"></div>

  <div class="abs feature" style="left:164px;top:1377px">
    <svg width="58" height="50" viewBox="0 0 58 50"><rect x="2" y="10" width="54" height="32" fill="none" stroke="var(--icon)" stroke-width="2"/><rect x="7" y="15" width="44" height="22" fill="none" stroke="var(--icon)" stroke-width="1.5"/><circle cx="29" cy="26" r="8" fill="none" stroke="var(--icon)" stroke-width="1.5"/><text x="29" y="30.5" font-size="12" text-anchor="middle" fill="var(--icon)" font-family="Lato,sans-serif">1</text></svg>
    <h3>Straightforward Pricing</h3>
    <p>We charge all our patients the same low rate - no surprises.</p>
  </div>
  <div class="abs feature" style="left:388px;top:1377px">
    <svg width="50" height="50" viewBox="0 0 50 50"><circle cx="25" cy="25" r="22" fill="none" stroke="var(--icon)" stroke-width="2"/><circle cx="25" cy="25" r="16" fill="none" stroke="var(--icon)" stroke-width="1.5"/><path d="M25 14 V26 H33" fill="none" stroke="var(--icon)" stroke-width="2"/></svg>
    <h3>Available when<br>you are</h3>
    <p>New patient appointments are available within 1 week.</p>
  </div>
  <div class="abs feature" style="left:615px;top:1377px">
    <svg width="54" height="50" viewBox="0 0 54 50"><rect x="2" y="6" width="50" height="32" rx="2" fill="none" stroke="var(--icon)" stroke-width="2"/><rect x="7" y="11" width="40" height="22" fill="none" stroke="var(--icon)" stroke-width="1.5"/><path d="M22 38 V44 H32 V38 M16 45 H38" fill="none" stroke="var(--icon)" stroke-width="2"/></svg>
    <h3>Hassle-free booking</h3>
    <p>Schedule your appointment online at your convenience - no need to call during business hours.</p>
  </div>
  <div class="abs feature" style="left:840px;top:1377px">
    <svg width="50" height="50" viewBox="0 0 50 50"><path d="M25 44 L6 24 C-2 14 8 2 18 8 C21 10 23 12 25 15 C27 12 29 10 32 8 C42 2 52 14 44 24 Z" fill="none" stroke="var(--icon)" stroke-width="2"/><path d="M25 38 L10 22 C5 15 12 8 19 12 C22 14 24 16 25 19 C26 16 28 14 31 12 C38 8 45 15 40 22 Z" fill="none" stroke="var(--icon)" stroke-width="1.2"/></svg>
    <h3>Devoted care</h3>
    <p>We schedule enough time at each visit to make sure all of your questions are answered.</p>
  </div>

  <div class="abs feature" style="left:164px;top:1612px">
    <svg width="46" height="50" viewBox="0 0 46 50"><rect x="2" y="8" width="42" height="38" rx="2" fill="none" stroke="var(--icon)" stroke-width="2"/><path d="M2 17 H44 M12 3 V12 M34 3 V12" stroke="var(--icon)" stroke-width="2"/><g fill="none" stroke="var(--icon)" stroke-width="1.3"><rect x="8" y="22" width="6" height="5"/><rect x="17" y="22" width="6" height="5"/><rect x="26" y="22" width="6" height="5"/><rect x="35" y="22" width="4" height="5"/><rect x="8" y="31" width="6" height="5"/><rect x="17" y="31" width="6" height="5"/><rect x="26" y="31" width="6" height="5"/><rect x="35" y="31" width="4" height="5"/></g></svg>
    <h3>Within your reach</h3>
    <p>Follow-up appointments may be done by video chat for your convenience.</p>
  </div>
  <div class="abs feature" style="left:388px;top:1612px">
    <svg width="30" height="50" viewBox="0 0 30 50"><path d="M15 2 V48 M25 12 C22 7 6 6 5 15 C4 24 26 23 25 34 C24 43 7 43 4 37" fill="none" stroke="var(--icon)" stroke-width="2"/></svg>
    <h3>Save on lab costs.</h3>
    <p>If paying upfront for labs, we offer discounted pricing of up to 90% off standard rates.</p>
  </div>
  <div class="abs feature" style="left:615px;top:1612px">
    <svg width="54" height="50" viewBox="0 0 54 50"><path d="M6 40 C6 18 26 8 50 8 C50 30 34 42 12 40 Z" fill="none" stroke="var(--icon)" stroke-width="2"/><path d="M2 46 L38 18" stroke="var(--icon)" stroke-width="1.5"/></svg>
    <h3>Save on medications</h3>
    <p>We offer deeply discounted wholesale price medications for our members at pharmacy on site.</p>
  </div>
  <div class="abs feature" style="left:840px;top:1612px;width:190px">
    <svg width="46" height="50" viewBox="0 0 46 50"><circle cx="23" cy="15" r="11" fill="none" stroke="var(--icon)" stroke-width="2"/><path d="M4 47 V40 C4 31 12 27 23 27 C34 27 42 31 42 40 V47 Z" fill="none" stroke="var(--icon)" stroke-width="2"/></svg>
    <h3>No middle man</h3>
    <p>We don’t bill any insurance plans so decisions about your healthcare will be made by you and Dr. Halvorsen, without the impersonal management that comes from third-party payers.</p>
  </div>
</section>

<section class="pricing">
  <div class="abs photo-ring"></div>
  <div class="abs photo" role="img" aria-label="Photograph of four friends with arms around each other, seen from behind at sunset"></div>
  <h2 class="abs price-title">OUR PRICING IS SIMPLE,<br>TRANSPARENT AND AFFORDABLE.</h2>
  <p class="abs price-sub">Membership Plan $80/mo, plus a one-time $99 enrollment fee.</p>
  <ul class="abs perks">
    <li><svg width="9" height="13" viewBox="0 0 9 13"><path d="M1 1 L7 6.5 L1 12" fill="none" stroke="var(--mint)" stroke-width="2.5"/></svg>Includes all appointments, no co-pay</li>
    <li><svg width="9" height="13" viewBox="0 0 9 13"><path d="M1 1 L7 6.5 L1 12" fill="none" stroke="var(--mint)" stroke-width="2.5"/></svg>Relaxed, unrushed visits</li>
    <li><svg width="9" height="13" viewBox="0 0 9 13"><path d="M1 1 L7 6.5 L1 12" fill="none" stroke="var(--mint)" stroke-width="2.5"/></svg>Direct communication with your doctor via phone, email, video chat 24/7</li>
    <li><svg width="9" height="13" viewBox="0 0 9 13"><path d="M1 1 L7 6.5 L1 12" fill="none" stroke="var(--mint)" stroke-width="2.5"/></svg>Convenient online scheduling (no need to call during business hours)</li>
    <li><svg width="9" height="13" viewBox="0 0 9 13"><path d="M1 1 L7 6.5 L1 12" fill="none" stroke="var(--mint)" stroke-width="2.5"/></svg>Wholesale price for labs and medications</li>
  </ul>
  <a class="abs learn" href="#">LEARN MORE</a>
</section>

<footer>
  <svg class="abs footer" width="1200" height="221" viewBox="0 0 1200 221" aria-hidden="true">
    <path d="M0 21 H530 C560 21 565 0 600 0 C635 0 640 21 670 21 H1200 V221 H0 Z" fill="var(--footer)"/>
  </svg>
  <nav class="abs foot-nav"><a href="#">HOME</a><a href="#">SPECIALTIES</a><a href="#">PRICING</a><a href="#">ABOUT US</a><a href="#">FAQ</a><a href="#">BLOG</a></nav>
  <p class="abs copy">© 2019 Company Name&nbsp; All right reserved</p>
  <div class="abs social">
    <span aria-label="Social profile 1"></span><span aria-label="Social profile 2"></span><span aria-label="Social profile 3"></span><span aria-label="Social profile 4"></span>
  </div>
</footer>

</body>
</html>
```